OpenHarbor Yoga Website Design

Business Logo - attached
5 pages being:
Home
About
Classes
Blog
Contact

Would like Scrolling webpage and yoga symbols to be used.

Must have's being:
Easy to navigate, Text needs to be able to be edited/updated, Enquire Now Links, More Information Links, be a secure site, SEO,

Please refer to attached document for the information for the body of the website.

Target Market(s)

Educators, Community Service, Health and Wellbeing, Mental Health

Industry/Entity Type

Yoga

Coding

Coded - Design and coding required

Number of Pages Required

5+ page

Font styles to use
Other font styles liked:
• Bella Bold BC

Colors
0094D4
00A9DD
6FCCEA
C7EBF8
E9F6FB
6B429C
8869AF
B7A5CE
E3DAEB
F3F0F8

Requirements
Must have
• Easy to navigate, Text needs to be able to be edited/updated, Enquire Now Links, More Information Links, be a secure site, SEO,
Nice to have
• Scrolling webpage, yoga symbols

```html
<!DOCTYPE html>
<html lang="en">
<head>
<meta charset="utf-8">
<title>OpenHarbor Yoga</title>
<link href="https://fonts.googleapis.com/css2?family=Amatic+SC:wght@700&family=Lora:wght@400;500;700&display=swap" rel="stylesheet">
<style>
:root{
  --purple:#6b2fc9;
  --purple-mid:#8869af;
  --lilac:#b7a5ce;
  --cyan:#1fb8d6;
  --sky:#6fccea;
  --ice:#eef9fb;
  --ink:#333333;
  --text:#555555;
  --white:#ffffff;
  --footer:#333333;
  --grad:linear-gradient(160deg,#6b2fc9 0%,#3f6fc9 55%,#1fc6d8 100%);
}
*{box-sizing:border-box;margin:0;padding:0}
html,body{width:1200px;height:2725px;overflow:hidden}
body{position:relative;background:var(--white);font-family:"Lora",Georgia,serif;color:var(--text)}
.abs{position:absolute}
a{text-decoration:none;color:inherit}

/* header */
.site-header{left:0;top:0;width:1200px;height:111px;background:var(--white);z-index:5}
.main-nav{left:111px;top:48px;display:flex;gap:33px;font-size:15.5px;font-weight:500;color:var(--ink)}
.main-nav .active{color:var(--cyan)}
.nav-contact{left:836px;top:48px;font-size:15.5px;font-weight:500;color:var(--ink)}
.social{display:flex;gap:8px}
.header-social{left:963px;top:40px}
.social .dot{width:36px;height:36px;border-radius:50%;background:var(--white);box-shadow:0 3px 8px rgba(0,0,0,.15);display:flex;align-items:center;justify-content:center}
.social .dot.filled{background:var(--grad)}
.brand-badge{left:517px;top:0;width:166px;height:166px;border-radius:50%;background:var(--white);z-index:6;display:flex;align-items:center;justify-content:center}
.brand-badge span{width:130px;height:130px;border-radius:50%;background:var(--purple);color:var(--white);display:flex;align-items:center;justify-content:center;text-align:center;font-size:16px;font-weight:500;line-height:1.3;padding:14px}

/* hero */
.hero{left:0;top:111px;width:1200px;height:702px}
.hero-title{left:111px;top:272px;font-family:"Amatic SC","Arial Narrow",sans-serif;font-size:56px;color:var(--purple);letter-spacing:1px}
.hero-lead{left:112px;top:344px;width:400px;font-size:20.5px;line-height:31.5px;color:var(--ink)}
.btn{height:48px;border-radius:24px;display:flex;align-items:center;justify-content:center;font-size:15px;font-weight:500}
.btn-primary{left:112px;top:464px;width:159px;background:var(--grad);color:var(--white)}
.btn-secondary{left:282px;top:464px;width:210px;background:var(--white);color:var(--cyan)}
.slider-dots{left:1137px;top:352px;display:flex;flex-direction:column;gap:13px}
.slider-dots i{width:7px;height:7px;border-radius:50%;background:var(--white);display:block}
.slider-dots i.on{box-shadow:0 0 0 3px rgba(255,255,255,.5)}

/* sections */
.section-title{left:0;width:1200px;text-align:center;font-family:"Amatic SC","Arial Narrow",sans-serif;font-size:58px;color:var(--purple);letter-spacing:1px}
.rule{left:553px;width:94px;height:3px;background:var(--cyan)}
.copy{left:145px;width:910px;text-align:center;font-size:17.5px;line-height:27.5px}
.copy p+p{margin-top:18px}

.benefits{left:0;top:1335px;width:1200px;height:1000px;background:var(--ice)}
.benefits-sub{left:0;top:1585px;width:1200px;text-align:center;font-size:21px;font-weight:500;color:var(--ink)}
.card{top:1646px;width:305px;height:574px;background:var(--white);border-radius:10px;box-shadow:0 4px 14px rgba(0,0,0,.06);padding:35px 24px 0}
.card-icon{width:88px;height:88px;border-radius:50%;background:var(--grad)}
.card h3{margin-top:25px;font-size:16px;font-weight:500;letter-spacing:1px;color:var(--ink)}
.card ul{list-style:none;margin-top:14px}
.card li{position:relative;padding-left:29px;font-size:15.5px;line-height:24px;margin-bottom:6px}
.card li::before{content:"";position:absolute;left:0;top:6px;width:12px;height:12px;border-radius:50%;background:var(--purple)}
.card li::after{content:"";position:absolute;left:3px;top:10px;border-left:5px solid var(--white);border-top:2.5px solid transparent;border-bottom:2.5px solid transparent}

/* footer */
.site-footer{left:0;top:2300px;width:1200px;height:425px}
.footer-brand{left:0;top:2410px;width:1200px;text-align:center;font-size:24px;font-weight:500;color:var(--lilac)}
.footer-nav{left:0;top:2555px;width:1200px;display:flex;justify-content:center;gap:30px;font-size:19px;font-weight:700;color:var(--white)}
.footer-nav .sep{font-weight:400}
.footer-mail{left:0;top:2593px;width:1200px;display:flex;justify-content:center;align-items:center;gap:12px;font-size:19px;color:var(--white)}
.footer-line{top:2654px;height:1px;background:#555}
.footer-social{left:559px;top:2636px}
.copyright{left:0;top:2692px;width:1200px;text-align:center;font-size:14px;color:var(--white)}
</style>
</head>
<body>

<!-- hero image -->
<svg class="abs hero" viewBox="0 0 1200 702" role="img" aria-label="Photo of a woman meditating with raised arms above misty green mountains">
  <defs>
    <linearGradient id="heroSky" x1="0" y1="0" x2="0" y2="1">
      <stop offset="0" stop-color="#7cc4e6"/>
      <stop offset="0.3" stop-color="#d6e6ee"/>
      <stop offset="0.55" stop-color="#8fb56a"/>
      <stop offset="1" stop-color="#4f7d2e"/>
    </linearGradient>
    <linearGradient id="arc" x1="0" y1="0" x2="1" y2="0">
      <stop offset="0" stop-color="#6b2fc9"/>
      <stop offset="1" stop-color="#b79ae6"/>
    </linearGradient>
  </defs>
  <path d="M0 0H1200V474Q600 842 0 474Z" fill="url(#heroSky)"/>
  <path d="M0 474Q600 842 1200 474" fill="none" stroke="url(#arc)" stroke-width="10"/>
</svg>

<header class="abs site-header">
  <nav class="abs main-nav">
    <a class="active" href="#">HOME</a><a href="#">ABOUT</a><a href="#">CLASSES</a><a href="#">BLOG</a>
  </nav>
  <a class="abs nav-contact" href="#">CONTACT</a>
  <div class="abs social header-social">
    <a class="dot filled" href="#" aria-label="Social page"></a>
    <a class="dot" href="#" aria-label="Photo page"></a>
    <a class="dot" href="#" aria-label="Email">
      <svg width="15" height="12" viewBox="0 0 15 12"><rect x="0.5" y="0.5" width="14" height="11" rx="1.5" fill="#333"/><path d="M1 1.5L7.5 6.5L14 1.5" stroke="#fff" stroke-width="1.4" fill="none"/></svg>
    </a>
  </div>
</header>
<div class="abs brand-badge"><span>OpenHarbor Yoga</span></div>

<h1 class="abs hero-title">OPENHARBOR YOGA</h1>
<p class="abs hero-lead">OpenHarbor Yoga believe that you are never too young to benefit from and fall in love with yoga.</p>
<a class="abs btn btn-primary" href="#">ENQUIRE NOW</a>
<a class="abs btn btn-secondary" href="#">MORE INFORMATION</a>
<div class="abs slider-dots"><i></i><i class="on"></i><i></i><i></i></div>

<!-- welcome -->
<h2 class="abs section-title" style="top:905px">WELCOME TO OPENHARBOR YOGA</h2>
<div class="abs rule" style="top:970px"></div>
<div class="abs copy" style="top:1006px">
  <p>OpenHarbor Yoga believe that you are never too young to benefit from and fall in love with yoga. My aim is to EMPOWER kids and teens to thrive by teaching life skills in Yoga, Mindfulness and Breathing techniques to deal with daily challenges and big emotions.</p>
  <p>OpenHarbor Yoga gives kids an opportunity to enjoy and experience yoga for themselves and primarily focuses on programs for Schools, Pre Schools and Early Learning Centres, Private Classes, Sporting Clubs, Martial Arts Schools, Scout Groups and Occupational Therapy Centres just to name a few. All classes are age appropriate and encourage children’s natural drive to learn, move, and be creative.</p>
</div>

<!-- benefits -->
<section class="abs benefits"></section>
<h2 class="abs section-title" style="top:1408px">BENEFITS OF YOGA</h2>
<div class="abs rule" style="top:1474px"></div>
<div class="abs copy" style="top:1507px"><p>The benefits of yoga can last a lifetime. It is my aim &amp; passion to introduce yoga to kids of all ages and backgrounds so that they can not only experience the benefits of yoga but fall in love with the practice.</p></div>
<p class="abs benefits-sub">Yoga benefits include:</p>

<article class="abs card" style="left:112px">
  <div class="card-icon" role="img" aria-label="Icon of a seated meditating figure"></div>
  <h3>HEALTHY BODIES</h3>
  <ul>
    <li>Develops strong, flexible and healthy bodies</li>
    <li>Promotes spinal alignment and good posture</li>
    <li>Builds energy and stamina</li>
    <li>Improves internal physical function - organs, digestion, elimination, circulation, &amp; blood flow.</li>
    <li>Helps breathing and lung capacity</li>
    <li>Teaches the enjoyment of movement</li>
    <li>Works the ‘whole’ body</li>
  </ul>
</article>
<article class="abs card" style="left:448px">
  <div class="card-icon" role="img" aria-label="Icon of a head with a lotus flower"></div>
  <h3>HEALTHY MINDS</h3>
  <ul>
    <li>Cultivates confidence and self-esteem</li>
    <li>Develops concentration and attention</li>
    <li>Clears the mind for better clarity and decision making</li>
    <li>Helps relax and sleep better</li>
    <li>Calms the nervous system</li>
    <li>Learns to cope with stressful situations</li>
    <li>Balances emotions</li>
  </ul>
</article>
<article class="abs card" style="left:783px">
  <div class="card-icon" role="img" aria-label="Icon of a dove carrying a branch"></div>
  <h3>HEALTHY SPIRITS</h3>
  <ul>
    <li>Fosters creativity, expression and imagination</li>
    <li>Cultivates kindness to themselves and others</li>
    <li>Cultivates respect for self and others</li>
    <li>Builds balance and inner quiet</li>
    <li>Builds inner strength and resilience</li>
    <li>Teaches self-awareness</li>
    <li>Focuses on positive self-talk</li>
  </ul>
</article>

<!-- footer -->
<svg class="abs site-footer" viewBox="0 0 1200 425" aria-hidden="true">
  <defs>
    <linearGradient id="footArc" x1="0" y1="0" x2="1" y2="0">
      <stop offset="0" stop-color="#6b2fc9"/>
      <stop offset="1" stop-color="#c2a8ee"/>
    </linearGradient>
  </defs>
  <path d="M0 237Q600 -135 1200 237V425H0Z" fill="#333333"/>
  <path d="M0 237Q600 -135 1200 237" fill="none" stroke="url(#footArc)" stroke-width="8"/>
</svg>
<p class="abs footer-brand">OpenHarbor Yoga</p>
<nav class="abs footer-nav">
  <a href="#">HOME</a><span class="sep">/</span><a href="#">ABOUT</a><span class="sep">/</span><a href="#">CLASSES</a><span class="sep">/</span><a href="#">BLOG</a><span class="sep">/</span><a href="#">CONTACT</a>
</nav>
<div class="abs footer-mail">
  <svg width="20" height="15" viewBox="0 0 20 15"><rect width="20" height="15" rx="2" fill="#1fb8d6"/><path d="M1 1.5L10 8L19 1.5" stroke="#333" stroke-width="1.6" fill="none"/></svg>
  <a href="#">hello@openharboryoga.example</a>
</div>
<div class="abs footer-line" style="left:112px;width:428px"></div>
<div class="abs footer-line" style="left:660px;width:428px"></div>
<div class="abs social footer-social">
  <a class="dot filled" href="#" aria-label="Social page"></a>
  <a class="dot" href="#" aria-label="Photo page"></a>
</div>
<p class="abs copyright">© Copyright 2023 OpenHarbor Yoga</p>

</body>
</html>
```